Business Card Design for sports performance / psychology company

You can see my website that this is based upon here:
http://www.trelvanedge.co.uk

More than happy to answer any additional questions that you might have

** Happy for any images from Pixelvault to be used. If I go with your design I will purchase the image for you to use

Target Market(s)

Football players

Industry/Entity Type

Business

Contact Information for Business Card

Name: Clive Arnott
Title: Clinical Hypnotherapist & Strategist
Email address: clive@trelvanedge.co.uk
Tel: 07912486015

Font styles to use
Other font styles liked:
• Same font as on website. I'm not actually sure what it is

Requirements
Must have
• Tagline:
• Steady mind, stronger game
• Don't put form down to chance
Nice to have
• Happy for designers to be creative
Should not have

```html
<!DOCTYPE html>
<html lang="en">
<head>
<meta charset="utf-8">
<title>Trelvan Edge – Business Card</title>
<link href="https://fonts.googleapis.com/css2?family=Lato:wght@300;400;700&display=swap" rel="stylesheet">
<style>
  :root {
    --stage: #222222;
    --navy: #231d4a;
    --ink: #2b2b33;
    --paper: #ffffff;
    --rule: #3a3a3a;
    --band-grey: #3a3a3c;
    --mark-grey: #d9d9de;
  }
  * { margin: 0; padding: 0; box-sizing: border-box; }
  html, body { width: 1189px; height: 1200px; overflow: hidden; background: var(--stage); }
  .canvas { position: relative; width: 1189px; height: 1200px; }

  .card {
    position: absolute;
    left: 171px;
    width: 856px;
    height: 487px;
    box-shadow: 6px 8px 14px rgba(0,0,0,0.55);
    overflow: hidden;
  }

  /* Front */
  .card--front { top: 68px; background: var(--navy); color: var(--paper); }
  .front__mark {
    position: absolute; left: 50%; top: 142px; width: 76px; height: 76px;
    margin-left: -38px; border-radius: 50%; background: var(--mark-grey);
  }
  .front__name {
    position: absolute; left: 0; right: 0; top: 238px; text-align: center;
    font-family: "Lato", sans-serif; font-weight: 400; font-size: 64px; line-height: 1;
  }
  .front__tagline {
    position: absolute; left: 0; right: 0; top: 319px; text-align: center;
    font-family: "Lato", sans-serif; font-weight: 400; font-size: 24px; line-height: 1;
  }

  /* Back */
  .card--back { top: 626px; background: var(--paper); color: var(--ink); }
  .back__brand {
    position: absolute; left: 38px; top: 60px; display: flex; align-items: center; gap: 32px;
  }
  .back__mark { width: 98px; height: 98px; background: var(--navy); }
  .back__name {
    font-family: "Lato", sans-serif; font-weight: 400; font-size: 54px;
    color: var(--navy); line-height: 1;
  }

  .person { position: absolute; right: 40px; top: 250px; text-align: right; font-family: "Lato", sans-serif; }
  .person__name { font-size: 34px; font-weight: 400; color: var(--navy); line-height: 1.1; }
  .person__name strong { font-weight: 700; }
  .person__title { font-size: 22px; font-weight: 300; color: var(--ink); margin-top: 2px; }

  .divider { position: absolute; left: 38px; right: 40px; top: 322px; height: 1px; background: var(--rule); }

  .contact { position: absolute; left: 38px; top: 354px; list-style: none; font-family: "Lato", sans-serif; }
  .contact__item { display: flex; align-items: center; gap: 10px; height: 28.5px; font-size: 24px; font-weight: 300; }
  .contact__icon { width: 23px; height: 23px; background: var(--navy); display: flex; align-items: center; justify-content: center; }
  .contact__icon svg { width: 17px; height: 17px; }
  .contact__domain { color: var(--navy); font-weight: 400; }

  .address {
    position: absolute; right: 40px; top: 343px; text-align: right;
    font-family: "Lato", sans-serif; font-weight: 300; font-size: 24px; line-height: 28px;
    font-style: normal;
  }

  .band { position: absolute; left: 0; bottom: 0; width: 856px; height: 40px; }
</style>
</head>
<body>
<main class="canvas">

  <section class="card card--front" aria-label="Card front">
    <div class="front__mark"></div>
    <h1 class="front__name">Trelvan Edge</h1>
    <p class="front__tagline">Steady mind, stronger game</p>
  </section>

  <section class="card card--back" aria-label="Card back">
    <div class="back__brand">
      <div class="back__mark"></div>
      <p class="back__name">Trelvan Edge</p>
    </div>

    <div class="person">
      <p class="person__name"><strong>Clive</strong> Arnott</p>
      <p class="person__title">Clinical Hypnotherapist &amp; Strategist</p>
    </div>

    <div class="divider"></div>

    <ul class="contact">
      <li class="contact__item">
        <span class="contact__icon"><svg viewBox="0 0 24 24" fill="none" stroke="#fff" stroke-width="2"><path d="M4 9c0-3 16-3 16 0v2h-4V9H8v2H4z"/><rect x="6" y="12" width="12" height="8"/></svg></span>
        07912486015
      </li>
      <li class="contact__item">
        <span class="contact__icon"><svg viewBox="0 0 24 24" fill="none" stroke="#fff" stroke-width="2"><rect x="3" y="5" width="18" height="14"/><path d="M3 5l9 8 9-8M3 19l7-7M21 19l-7-7"/></svg></span>
        clive@trelvanedge.co.uk
      </li>
      <li class="contact__item">
        <span class="contact__icon"><svg viewBox="0 0 24 24" fill="none" stroke="#fff" stroke-width="1.8"><circle cx="12" cy="12" r="9"/><ellipse cx="12" cy="12" rx="4" ry="9"/><path d="M3 12h18M5 7h14M5 17h14"/></svg></span>
        <span>www.<span class="contact__domain">trelvanedge</span>.co.uk</span>
      </li>
    </ul>

    <address class="address">
      Drakewell Science Park<br>
      Drakewell &amp; Beckford Street<br>
      London
    </address>

    <svg class="band" viewBox="0 0 856 40" preserveAspectRatio="none">
      <polygon points="0,15 484,15 474,40 0,40" fill="var(--band-grey)"/>
      <polygon points="498,0 856,0 856,40 484,40" fill="var(--navy)"/>
    </svg>
  </section>

</main>
</body>
</html>
```